Brisk Hollow toothpaste tube design

Design a Brisk Hollow tube design for our all natural toothpaste. The toothpaste is 100% natural with a smooth marshmallow consistency. It's unique because it's not pastelike at all. The all natural flavors make the toothpaste taste great. The toothpaste is smooth yet still leaves your mouth feeling squeaky clean. We want to market this as an all natural family toothpaste.

The flavor is Mint. (possibly called "Breezy Mint")

We have included our logo (eps & jpg), information that goes on the back of the tube, and the artwork template from the tube supplier for the 4.2oz tube.

We like a vintage earthy retro look and feel but we are not limited to this.

The tubes stand upright as shown in the picture of File 4.
Updates

The finished artwork must include anĀ adobe illustratorĀ file.

I would like to thank all of the designers for their work on this project. We had a difficult time making a decision since all of the designs were very close to what we expected.

Sincerely,

Glen

Target Market(s)

The target market is families that desire an all natural toothpaste. We will be stressing the 100% natural and great taste.

Requirements
Must have
• Three colors maximum due to tube manufacture restrictions.

Must have "100% natural" and "fluoride free" on front of tube. A reference to the great taste or flavor is also important.

Must say 4.2 oz on the front of the tube, centered, at the bottom.
Nice to have
• Fun, colorful packaging that will stand out. Go to your local store and stand in front of the tootpaste shelves, give us something different!
Should not have
• We do not want a lot of red or blue because these are predominate colors already in use on toothpaste tubes and boxes.

```html
<!DOCTYPE html>
<html lang="en">
<head>
<meta charset="utf-8">
<title>Brisk Hollow Toothpaste – Tube Range</title>
<link rel="stylesheet" href="https://fonts.googleapis.com/css2?family=Arimo:wght@400;700&family=Gochi+Hand&display=swap">
<style>
  :root {
    --page: #ffffff;
    --tube: #fdfdfd;
    --tube-edge: #e4e6e4;
    --crimp-line: #eceeed;
    --green: #2f9a48;
    --green-deep: #1f7d37;
    --green-light: #5bb86a;
    --ink-light: #ffffff;
    --swatch-mint: #c4dcc2;
    --swatch-tangerine: #f1c57c;
    --swatch-strawberry: #e8a386;
  }
  * { box-sizing: border-box; margin: 0; padding: 0; }
  html, body {
    width: 1200px; height: 898px; overflow: hidden;
    background: var(--page);
    font-family: "Arimo", Arial, sans-serif;
  }
  .range {
    position: relative; width: 1200px; height: 898px;
  }
  .tube {
    position: absolute; top: 30px; width: 308px; height: 804px;
  }
  .tube--mint { left: 142px; }
  .tube--tangerine { left: 465px; }
  .tube--strawberry { left: 788px; }

  .tube__crimp {
    position: absolute; left: 0; top: 0; width: 308px; height: 52px;
    background: repeating-linear-gradient(180deg, var(--tube) 0 4px, var(--crimp-line) 4px 5px);
    border: 1px solid var(--tube-edge); border-bottom: none;
  }
  .tube__body {
    position: absolute; left: 0; top: 52px; width: 308px; height: 690px;
    background: var(--tube);
    border: 1px solid var(--tube-edge); border-top: none;
    border-radius: 0 0 40px 40px;
    overflow: hidden;
  }
  .tube__cap {
    position: absolute; left: 78px; top: 742px; width: 152px; height: 62px;
    background: var(--tube);
    border: 1px solid var(--tube-edge); border-top: none;
    border-radius: 0 0 6px 6px;
  }

  .brand {
    position: absolute; top: 52px; left: 0; width: 100%;
    text-align: center; color: var(--green-deep);
  }
  .brand__name {
    display: inline-flex; align-items: center; gap: 8px;
    font-weight: 700; font-size: 38px; line-height: 1;
  }
  .brand__dot {
    width: 16px; height: 16px; border-radius: 50%; background: var(--green-deep);
  }
  .brand__tagline {
    margin-top: 8px; font-size: 12px; font-weight: 700; letter-spacing: 0.3px;
  }

  .meadow {
    position: absolute; left: 0; top: 198px; width: 100%; height: 36px;
    background: linear-gradient(180deg, rgba(47,154,72,0) 0%, var(--green-light) 60%, var(--green) 100%);
  }
  .panel {
    position: absolute; left: 0; top: 234px; width: 100%; height: 456px;
    background: var(--green);
  }
  .flavour {
    position: absolute; left: 18px; top: 14px; width: 272px; height: 46px;
    border-radius: 4px;
    font-family: "Gochi Hand", cursive; font-size: 31px; line-height: 46px;
    color: var(--ink-light); text-align: center; letter-spacing: 1px;
  }
  .tube--mint .flavour { background: var(--swatch-mint); }
  .tube--tangerine .flavour { background: var(--swatch-tangerine); }
  .tube--strawberry .flavour { background: var(--swatch-strawberry); }

  .claims {
    position: absolute; left: 0; top: 76px; width: 100%;
    list-style: none; text-align: center;
    color: var(--ink-light); font-weight: 700; font-size: 16.5px; line-height: 23px;
  }
  .claims li::before { content: "• "; }

  .seal {
    position: absolute; left: 172px; top: 236px; width: 100px; height: 100px;
    border-radius: 50%; border: 3px solid var(--ink-light);
  }
  .net-weight {
    position: absolute; left: 0; top: 376px; width: 100%;
    text-align: center; color: var(--ink-light); font-size: 17px;
  }
</style>
</head>
<body>
<main class="range">

  <section class="tube tube--mint">
    <div class="tube__crimp"></div>
    <div class="tube__body">
      <header class="brand">
        <div class="brand__name"><span class="brand__dot"></span>Brisk Hollow</div>
        <p class="brand__tagline">MAKE EVERY DAY A BRISK HOLLOW DAY</p>
      </header>
      <div class="meadow" role="img" aria-label="Grass and wildflower silhouette along the top of the green panel"></div>
      <div class="panel">
        <p class="flavour">breezy mint</p>
        <ul class="claims">
          <li>100% Natural toothpaste</li>
          <li>Natural flavours</li>
          <li>Flouride free</li>
          <li>Smooth, great taste</li>
          <li>For all the family</li>
        </ul>
        <div class="seal" aria-hidden="true"></div>
        <p class="net-weight">4.2oz</p>
      </div>
    </div>
    <div class="tube__cap"></div>
  </section>

  <section class="tube tube--tangerine">
    <div class="tube__crimp"></div>
    <div class="tube__body">
      <header class="brand">
        <div class="brand__name"><span class="brand__dot"></span>Brisk Hollow</div>
        <p class="brand__tagline">MAKE EVERY DAY A BRISK HOLLOW DAY</p>
      </header>
      <div class="meadow" role="img" aria-label="Grass and wildflower silhouette along the top of the green panel"></div>
      <div class="panel">
        <p class="flavour">tasty tangerine</p>
        <ul class="claims">
          <li>100% Natural toothpaste</li>
          <li>Natural flavours</li>
          <li>Flouride free</li>
          <li>Smooth, great taste</li>
          <li>For all the family</li>
        </ul>
        <div class="seal" aria-hidden="true"></div>
        <p class="net-weight">4.2oz</p>
      </div>
    </div>
    <div class="tube__cap"></div>
  </section>

  <section class="tube tube--strawberry">
    <div class="tube__crimp"></div>
    <div class="tube__body">
      <header class="brand">
        <div class="brand__name"><span class="brand__dot"></span>Brisk Hollow</div>
        <p class="brand__tagline">MAKE EVERY DAY A BRISK HOLLOW DAY</p>
      </header>
      <div class="meadow" role="img" aria-label="Grass and wildflower silhouette along the top of the green panel"></div>
      <div class="panel">
        <p class="flavour">smooth strawberry</p>
        <ul class="claims">
          <li>100% Natural toothpaste</li>
          <li>Natural flavours</li>
          <li>Flouride free</li>
          <li>Smooth, great taste</li>
          <li>For all the family</li>
        </ul>
        <div class="seal" aria-hidden="true"></div>
        <p class="net-weight">4.2oz</p>
      </div>
    </div>
    <div class="tube__cap"></div>
  </section>

</main>
</body>
</html>
```